Dermatologist office in Brasilia. My with "target customers" are specially women.

I’m a dermatologist who works since 2006 in Brasilia. In 2017 I decided to change and improve my career. I decided to work more with cosmetics (Lumiqa and fillers), I still work with clinical and surgical dermatology.
Most of my patients are women but 20-30% are children and men.
I would like to see designs that use a butterfly and the color aquamarine with details in gold.

Industry/Entity Type

Cosmetics

Font styles to use
Sans Serif

Colors
33b8a4
87cfc6
cfeae6
85cae6

Requirements
Must have
• My project must have my name (Harumi Okeda) and my medical specialty (Dermatologista)
Nice to have
• The colors I prefer are aquamarine or Corvell Jade Tin.
• I also prefer a butterfly that means transformation and a new life.
• I prefer a sofisticated and also minimalist design.

```html
<!DOCTYPE html>
<html lang="en">
<head>
<meta charset="utf-8">
<title>Harumi Okeda — Dermatologist Stationery</title>
<link rel="stylesheet" href="https://fonts.googleapis.com/css2?family=Jost:wght@400;500&family=Rubik:wght@300;400&display=swap">
<style>
  :root{
    --teal:#33b8a4;
    --teal-soft:#87cfc6;
    --teal-pale:#cfeae6;
    --sky:#85cae6;
    --ink:#2b2b2b;
    --text:#555555;
    --olive:#3d4a26;
    --card-dark:#2b2b2b;
    --paper:#ffffff;
    --bg:#ffffff;
  }
  *{box-sizing:border-box;margin:0;padding:0}
  html,body{width:1200px;height:1200px;overflow:hidden;background:var(--bg)}
  body{position:relative;font-family:"Rubik",sans-serif;color:var(--text)}
  .piece{position:absolute;background:var(--paper);overflow:hidden;border:1px solid #ececec}
  .brand{position:absolute;left:0;right:0;text-align:center}
  .brand-dot{display:block;margin:0 auto 16px;width:44px;height:44px;border-radius:50%;background:var(--teal)}
  .brand-name{font-family:"Jost",sans-serif;font-weight:400;letter-spacing:.42em;text-transform:uppercase;color:var(--ink);white-space:nowrap}
  .brand-role{font-family:"Jost",sans-serif;font-weight:500;letter-spacing:.5em;text-transform:uppercase;color:var(--ink);margin-top:6px;white-space:nowrap}

  /* dark front card */
  .card-dark{left:47px;top:249px;width:400px;height:228px;background:var(--card-dark);border:none}
  .card-dark .brand{top:52px}
  .card-dark .brand-name{font-size:15px;color:#fff}
  .card-dark .brand-role{font-size:7.5px;color:#fff}

  /* contact back card */
  .card-contact{left:46px;top:515px;width:402px;height:229px}
  .card-contact .accent-bar{position:absolute;left:2px;top:38px;width:3px;height:33px;background:var(--teal)}
  .card-contact .holder{position:absolute;left:21px;top:41px}
  .holder-name{font-size:15.5px;font-weight:400;color:#444;text-transform:uppercase}
  .holder-role{font-size:9px;font-weight:300;color:var(--teal);margin-top:3px}
  .card-contact .brand{left:auto;right:14px;width:150px;top:20px}
  .card-contact .brand-dot{width:28px;height:28px;margin-bottom:10px}
  .card-contact .brand-name{font-size:9.5px}
  .card-contact .brand-role{font-size:4.5px;margin-top:4px}
  .contact-list{position:absolute;list-style:none;font-size:9.5px;line-height:12.8px;font-weight:300;color:#555}
  .contact-list li{display:flex;align-items:center;gap:6px}
  .contact-list svg{width:7px;height:7px;flex:none}
  .card-contact .contact-list{left:22px;top:150px}
  .address{position:absolute;font-size:9.5px;line-height:12.8px;font-weight:300;color:#555}
  .card-contact .address{left:243px;top:162px}
  .footer-band{position:absolute;left:0;bottom:0;width:100%;background:linear-gradient(90deg,var(--teal) 0%,var(--teal-soft) 45%,var(--teal-pale) 100%)}
  .card-contact .footer-band{height:14px}

  /* light front card */
  .card-light{left:46px;top:810px;width:402px;height:229px}
  .card-light .brand{top:48px}
  .card-light .brand-name{font-size:16px}
  .card-light .brand-role{font-size:7.5px}

  /* letterhead */
  .letterhead{left:497px;top:131px;width:653px;height:909px}
  .letterhead .brand{left:35px;right:auto;top:34px;text-align:left}
  .letterhead .brand-dot{margin:0 0 22px 74px;width:60px;height:60px}
  .letterhead .brand-name{font-size:17.5px}
  .letterhead .brand-role{font-size:8px;margin:6px 0 0 34px}
  .date{position:absolute;right:34px;top:126px;font-size:10px;font-weight:300;color:#555}
  .greeting{position:absolute;left:34px;top:222px;font-family:"Rubik",sans-serif;font-weight:300;font-size:24px;color:var(--olive);letter-spacing:.02em}
  .body-copy{position:absolute;left:35px;width:588px;font-size:10.9px;line-height:14px;font-weight:300;color:#444;text-align:justify}
  .copy-1{top:273px}
  .copy-2{top:411px}
  .copy-3{top:567px}
  .signature-mark{position:absolute;left:40px;top:676px;width:70px;height:28px;border-radius:4px;background:linear-gradient(90deg,#eef1ea,#f7f8f4)}
  .signature-line{position:absolute;left:40px;top:710px;width:106px;border-top:1px solid #999}
  .signature-label{position:absolute;left:38px;top:720px;font-size:12.5px;font-weight:300;color:#555}
  .letterhead .contact-list{left:38px;top:796px;font-size:10.4px;line-height:14px}
  .letterhead .address{right:38px;top:810px;font-size:10.4px;line-height:14px;width:160px}
  .letterhead .footer-band{height:26px}
</style>
</head>
<body>

<section class="piece card-dark" aria-label="Business card front, dark">
  <div class="brand">
    <span class="brand-dot"></span>
    <p class="brand-name">Harumi Okeda</p>
    <p class="brand-role">Dermatologist</p>
  </div>
</section>

<section class="piece card-contact" aria-label="Business card back">
  <span class="accent-bar"></span>
  <div class="holder">
    <p class="holder-name">Harumi Okeda</p>
    <p class="holder-role">Dermatologist</p>
  </div>
  <div class="brand">
    <span class="brand-dot"></span>
    <p class="brand-name">Harumi Okeda</p>
    <p class="brand-role">Dermatologist</p>
  </div>
  <ul class="contact-list">
    <li><svg viewBox="0 0 10 10"><path d="M2 1l2 2-1 1.3c.6 1.2 1.5 2.1 2.7 2.7L7 6l2 2-1.2 1.3C4.5 9 1 5.5.8 2.2z" fill="var(--teal)"/></svg>0431 555 019</li>
    <li><svg viewBox="0 0 10 10"><rect x=".8" y="2" width="8.4" height="6" fill="none" stroke="var(--teal)"/><path d="M1 2.4l4 3 4-3" fill="none" stroke="var(--teal)"/></svg>info@harumiokeda.com.au</li>
    <li><svg viewBox="0 0 10 10"><circle cx="5" cy="5" r="4" fill="none" stroke="var(--teal)"/><path d="M1 5h8M5 1c-2 2.5-2 5.5 0 8M5 1c2 2.5 2 5.5 0 8" fill="none" stroke="var(--teal)" stroke-width=".7"/></svg>www.harumiokeda.com.au</li>
  </ul>
  <p class="address">418/B Larkin Row, Downtown,<br>New York, USA</p>
  <div class="footer-band" role="img" aria-label="Decorative aquamarine wave band"></div>
</section>

<section class="piece card-light" aria-label="Business card front, light">
  <div class="brand">
    <span class="brand-dot"></span>
    <p class="brand-name">Harumi Okeda</p>
    <p class="brand-role">Dermatologist</p>
  </div>
</section>

<section class="piece letterhead" aria-label="Letterhead">
  <div class="brand">
    <span class="brand-dot"></span>
    <p class="brand-name">Harumi Okeda</p>
    <p class="brand-role">Dermatologist</p>
  </div>
  <p class="date">Date: 20/10/2017</p>
  <h1 class="greeting">HELLO</h1>
  <p class="body-copy copy-1">Lorem ipsum dolor sit amet, tale tamquam accumsan pri ex, vim in assum nulla labitur, populo facilisis voluptatum eu sit. Nam fugit animal habemus ei, vim idque lucilius ex, quo ei sensibus liberavisse. Eruditi phaedrum vituperatori bus te eos. Cetero singulis reformidans nam ne. Has ea exerci timeam. Justo malis no has, sit eu iudicabit quaerend Lorem ipsum dolor sit amet, tale tamquam accumsan pri ex, vim in assum nulla labitur, populo facilisis voluptatum eu sit. Nam fugit animal habemus ei, vim idque lucilius ex, quo ei sensibus liberavisse. Eruditi phaedrum vituperatori bus te eos. Cetero singulis reformidans nam ne. Has ea exerci timeam. Justo malis no has, sit eu iudicabit quaerend eu sit. Nam fugit animal habemus ei, vim idque lucilius ex, quo ei sensibus liberavisse. Eruditi phaedrum vituperatori bus te eos. Cetero singulis reformidans nam ne. Has ea exerci timeam.</p>
  <p class="body-copy copy-2">Lorem ipsum dolor sit amet, tale tamquam accumsan pri ex, vim in assum nulla labitur, populo facilisis voluptatum eu sit. Nam fugit animal habemus ei, vim idque lucilius ex, quo ei sensibus liberavisse. Eruditi phaedrum vituperatori bus te eos. Cetero singulis reformidans nam ne. Has ea exerci timeam. Justo malis no has, sit eu iudicabit quaerend Lorem ipsum dolor sit amet, tale tamquam accumsan pri ex, vim in assum nulla labitur, populo facilisis voluptatum eu sit. Nam fugit animal habemus ei, vim idque lucilius ex, quo ei sensibus liberavisse. Eruditi phaedrum vituperatori bus te eos. Cetero singulis reformidans nam ne. Has ea exerci timeam. Justo malis no has, sit eu iudicabit quaerend eu sit. Nam fugit animal habemus ei, vim idque lucilius ex, quo ei sensibus liberavisse. Eruditi phaedrum vituperatori bus te eos. Cetero singulis reformidans nam ne. Has ea exerci timeam. Justo malis no has, sit eu iudicabit quaerend Lorem ipsum dolor sit amet, tale.</p>
  <p class="body-copy copy-3">Nam fugit animal habemus ei, vim idque lucilius ex, quo ei sensibus liberavisse. Eruditi phaedrum vituperatori bus te eos. Cetero singulis reformidans nam ne. Has ea exerci timeam. Justo malis no has, sit eu iudicabit quaerend Lorem ipsum dolor sit amet, tale</p>
  <div class="signature-mark" role="img" aria-label="Handwritten signature"></div>
  <span class="signature-line"></span>
  <p class="signature-label">Signature</p>
  <ul class="contact-list">
    <li><svg viewBox="0 0 10 10"><path d="M2 1l2 2-1 1.3c.6 1.2 1.5 2.1 2.7 2.7L7 6l2 2-1.2 1.3C4.5 9 1 5.5.8 2.2z" fill="var(--teal)"/></svg>0431 555 019</li>
    <li><svg viewBox="0 0 10 10"><rect x=".8" y="2" width="8.4" height="6" fill="none" stroke="var(--teal)"/><path d="M1 2.4l4 3 4-3" fill="none" stroke="var(--teal)"/></svg>info@brenlowclinic.com.au</li>
    <li><svg viewBox="0 0 10 10"><circle cx="5" cy="5" r="4" fill="none" stroke="var(--teal)"/><path d="M1 5h8M5 1c-2 2.5-2 5.5 0 8M5 1c2 2.5 2 5.5 0 8" fill="none" stroke="var(--teal)" stroke-width=".7"/></svg>www.brenlowclinic.com.au</li>
  </ul>
  <p class="address">418/B Larkin Row, Downtown,<br>New York, USA</p>
  <div class="footer-band" role="img" aria-label="Decorative aquamarine wave band"></div>
</section>

</body>
</html>
```